1 Page for Computer Repair Website

Looking for a 1 page website with a design that compliments the business card and pamphlet that have already been made (attached files). It should look business professional and easy to read. Email and phone number should be somewhere near the top of the website, visible when the page loads. I don't want any forms for people to mess with. No "Contact Us" form or entering in email for newsletter. Customers will just be looking at this site to confirm we are professionals and have our business in order.

Target Market(s)

Home and small business

Industry/Entity Type

Computer Repair

Coding

Coded - Design and coding required

Number of Pages Required

1 page

Font styles to use
Other font styles liked:
• Helvetica variations used in pamphlet and card

Colors
0455a3
cfdeed
85abd2
3276b5
85cae6
ffffff

Requirements
Must have
• Compliment the pamphlet and business card in color choices and font use. Pleasing to the eye and easy to read through categories and text.
Should not have
• Forms. No "enter name and email here" or anything of the sort.

```html
<!DOCTYPE html>
<html lang="en">
<head>
<meta charset="utf-8">
<title>ByteFix Computer Repair</title>
<link href="https://fonts.googleapis.com/css2?family=Open+Sans:wght@300;400;600;700&display=swap" rel="stylesheet">
<style>
:root{
  --blue:#0455a3;
  --blue-mid:#3276b5;
  --blue-soft:#85abd2;
  --blue-sky:#85cae6;
  --blue-pale:#cfdeed;
  --white:#ffffff;
  --navy:#0a2d57;
  --ink:#333a44;
  --grey:#8a9099;
}
*{margin:0;padding:0;box-sizing:border-box}
html,body{width:1200px;height:2296px;overflow:hidden;background:var(--white)}
body{font-family:"Open Sans",Helvetica,Arial,sans-serif;color:var(--ink)}
.page{position:relative;width:1200px;height:2296px;overflow:hidden}
.abs{position:absolute}

/* header */
.topbar{left:0;top:0;width:1200px;height:64px;background:rgba(255,255,255,.92);border-bottom:1px solid var(--blue-pale);z-index:3}
.nav{left:64px;top:10px;display:flex;gap:6px;z-index:4}
.nav a{display:block;padding:12px 12px;font-size:13px;color:var(--blue);text-decoration:none;text-transform:uppercase}
.nav a.active{background:var(--blue);color:var(--white)}
.brand{left:484px;top:0;width:232px;height:150px;background:rgba(255,255,255,.94);border:1px solid var(--blue-pale);border-top:0;display:flex;align-items:center;justify-content:center;z-index:4}
.brand span{font-size:50px;font-weight:700;color:var(--blue);letter-spacing:1px}
.contact-top{top:20px;display:flex;align-items:center;gap:8px;font-size:13px;color:var(--blue);z-index:4}
.contact-top svg{width:22px;height:22px}

/* hero */
.hero-photo{left:0;top:0;width:1200px;height:660px;background:linear-gradient(110deg,#d6dde4 0%,#b7c2cc 35%,#8f7a6c 60%,#c9c9cf 100%)}
.hero-panel{left:258px;top:240px;width:684px;height:300px;background:rgba(255,255,255,.72);text-align:center;padding-top:36px}
.hero-panel h1{font-weight:400;font-size:30px;line-height:42px;color:var(--blue-mid);text-transform:uppercase}
.divider{display:block;margin:14px auto}
.hero-panel p{font-size:13px;line-height:20px;color:var(--ink);width:440px;margin:0 auto}
.dots{display:flex;gap:8px;justify-content:center}
.dots i{display:block;width:32px;height:5px;background:var(--blue-soft)}
.dots i.on{background:var(--blue)}

/* about */
.about{left:0;top:660px;width:1200px;height:360px;background:linear-gradient(90deg,#9fb3c6 0%,#c4d3e2 45%,var(--blue-pale) 60%,#dfe8f2 100%)}
.about-photo{left:0;top:660px;width:620px;height:360px;background:linear-gradient(90deg,#7f95ab 0%,#a7b9cc 55%,rgba(207,222,237,0) 100%)}
.about-text{left:640px;top:690px;width:460px;text-align:center}
.about-text h2{font-weight:400;font-size:38px;color:var(--blue);text-transform:uppercase}
.about-text .rule{height:1px;background:var(--blue-mid);margin:6px 0 20px}
.about-text p{font-size:13px;line-height:22px;color:var(--ink)}
.btn{display:inline-block;background:var(--blue);color:var(--white);font-size:13px;padding:14px 30px;margin-top:26px}

/* services */
.services-bg{left:0;top:1020px;width:1200px;height:680px;background:radial-gradient(circle at 50% 60%,#2b5f8e 0%,#123a63 45%,#0a1f3a 100%)}
.section-title{width:1200px;left:0;text-align:center;font-weight:300;font-size:42px;text-transform:uppercase}
.card-photo{width:164px;height:164px;border:6px solid var(--white);box-shadow:0 2px 6px rgba(0,0,0,.4)}
.card{width:328px;height:220px;background:var(--white);text-align:center;padding:52px 34px 0}
.card h3{font-weight:400;font-size:20px;color:var(--blue)}
.card p{font-size:12px;line-height:18px;color:var(--ink);margin-top:10px}
.card a{display:inline-block;margin-top:10px;font-size:13px;color:var(--blue);border-bottom:1px solid var(--blue)}
.btn-ghost{left:520px;top:1604px;width:160px;height:52px;border:2px solid var(--white);color:var(--white);font-size:14px;display:flex;align-items:center;justify-content:center}

/* why */
.why p{font-size:13px;line-height:24px;color:var(--ink);width:440px}
.why .author{font-size:12px;color:var(--grey);margin-top:14px}

/* contact band */
.contact-band{left:0;top:2020px;width:1200px;height:220px;background:linear-gradient(90deg,#0b3566 0%,#1b4f84 50%,#0b3566 100%)}
.icon-box{width:100px;height:100px;background:#c9ced4;display:flex;align-items:center;justify-content:center}
.band-text{font-size:28px;color:var(--white);font-weight:400}
.footer-nav{left:400px;top:2190px;display:flex;gap:28px;font-size:12px;color:var(--white);text-transform:uppercase}
.footer-nav span.active{border-bottom:1px solid var(--white)}
.bottombar{left:0;top:2240px;width:1200px;height:56px;background:var(--navy);color:var(--blue-pale);font-size:12px;padding:20px 0 0 30px}
.socials{right:40px;top:2258px;display:flex;gap:12px}
.socials i{display:block;width:18px;height:18px;border-radius:50%;background:var(--blue-sky)}
</style>
</head>
<body>
<div class="page">

  <!-- hero -->
  <div class="abs hero-photo" role="img" aria-label="Photo of a smiling technician working at a computer in a bright office"></div>
  <div class="abs topbar"></div>
  <nav class="abs nav">
    <a class="active">Home</a><a>About Us</a><a>Services</a><a>Contact Us</a>
  </nav>
  <div class="abs brand"><span>ByteFix</span></div>
  <div class="abs contact-top" style="left:780px">
    <svg viewBox="0 0 24 24"><rect x="2" y="5" width="20" height="14" fill="none" stroke="#0455a3" stroke-width="1.6"/><path d="M2 5l10 8 10-8" fill="none" stroke="#0455a3" stroke-width="1.6"/></svg>
    info@company.com
  </div>
  <div class="abs contact-top" style="left:990px">
    <svg viewBox="0 0 24 24"><path d="M6 3l3 0 2 5-2 2c1 2.5 3 4.5 5 5l2-2 5 2v3c0 1-1 2-2 2C10 20 4 14 4 5c0-1 1-2 2-2z" fill="#0455a3"/></svg>
    1234567890
  </div>

  <div class="abs hero-panel">
    <h1>We provide a best computer<br>services</h1>
    <svg class="divider" width="300" height="14" viewBox="0 0 300 14"><line x1="0" y1="7" x2="138" y2="7" stroke="#0455a3"/><line x1="162" y1="7" x2="300" y2="7" stroke="#0455a3"/><path d="M144 12l6-10 6 10" fill="none" stroke="#0455a3" stroke-width="1.5"/></svg>
    <p>Lorem Ipsum is simply dummy text of the printing and typesetting industry. Lorem Ipsum has been the industry's standard dummy text ever.</p>
    <div class="dots" style="margin-top:20px"><i></i><i class="on"></i><i></i></div>
  </div>

  <!-- about -->
  <div class="abs about"></div>
  <div class="abs about-photo" role="img" aria-label="Photo of a young technician with glasses beside a glowing screen"></div>
  <div class="abs about-text">
    <h2>Know About Us</h2>
    <div class="rule"></div>
    <p>Lorem Ipsum is simply dummy text of the printing and typesetting industry. Lorem Ipsum has been the industry's standard dummy text ever since the 1500s, when an unknown printer took a galley of type.</p>
    <span class="btn">Read More</span>
  </div>

  <!-- services -->
  <div class="abs services-bg" role="img" aria-label="Dark blue background photo of a circuit board"></div>
  <h2 class="abs section-title" style="top:1050px;color:var(--white)">Our Services</h2>
  <svg class="abs" style="left:450px;top:1112px" width="300" height="14" viewBox="0 0 300 14"><line x1="0" y1="7" x2="138" y2="7" stroke="#ffffff"/><line x1="162" y1="7" x2="300" y2="7" stroke="#ffffff"/><path d="M144 12l6-10 6 10" fill="none" stroke="#ffffff" stroke-width="1.5"/></svg>

  <div class="abs card-photo" style="left:74px;top:1180px;background:linear-gradient(135deg,#e9e4df,#b58f78)" role="img" aria-label="Photo of a smiling support agent with a headset"></div>
  <div class="abs card" style="left:72px;top:1340px">
    <h3>Honest Service</h3>
    <p>Our certified technicians give an honest estimate. No pressure to upgrade products or services you don't need or want.</p>
    <a>Know More</a>
  </div>

  <div class="abs card-photo" style="left:434px;top:1180px;background:linear-gradient(135deg,#b22a1e,#3a3a3a)" role="img" aria-label="Photo of a laptop showing a virus warning"></div>
  <div class="abs card" style="left:436px;top:1340px">
    <h3>Malware/Virus Removal</h3>
    <p>Infections can come from many places and sometimes antivirus just isn't enough. We clean your system back to top shape.</p>
    <a>Know More</a>
  </div>

  <div class="abs card-photo" style="left:798px;top:1180px;background:linear-gradient(135deg,#dfe6ec,#6b7c8c)" role="img" aria-label="Photo of a desktop computer set up in a home office"></div>
  <div class="abs card" style="left:800px;top:1340px">
    <h3>In-Home Installation</h3>
    <p>All our services come with pick-up and drop-off installation. You won't be left to set up wireless.</p>
    <a>Know More</a>
  </div>

  <div class="abs btn-ghost">View All</div>

  <!-- why choose us -->
  <h2 class="abs section-title" style="top:1732px;color:var(--blue-mid)">Why Choose Us</h2>
  <svg class="abs" style="left:450px;top:1794px" width="300" height="14" viewBox="0 0 300 14"><line x1="0" y1="7" x2="138" y2="7" stroke="#0455a3"/><line x1="162" y1="7" x2="300" y2="7" stroke="#0455a3"/><path d="M144 12l6-10 6 10" fill="none" stroke="#0455a3" stroke-width="1.5"/></svg>
  <div class="abs why" style="left:80px;top:1850px">
    <p>Lorem Ipsum is simply dummy text of the printing and typesetting industry. Lorem Ipsum has been the industry's standard dummy text ever.</p>
    <p class="author">- XYZ Name</p>
  </div>
  <div class="abs why" style="left:680px;top:1850px">
    <p>Lorem Ipsum is simply dummy text of the printing and typesetting industry. Lorem Ipsum has been the industry's standard dummy text ever.</p>
    <p class="author">- XYZ Name</p>
  </div>
  <div class="abs dots" style="left:0;width:1200px;top:1976px"><i></i><i class="on"></i><i></i><i></i></div>

  <!-- contact band -->
  <div class="abs contact-band" role="img" aria-label="Dark blue background photo of a city at night"></div>
  <div class="abs icon-box" style="left:240px;top:2060px">
    <svg width="54" height="40" viewBox="0 0 54 40"><rect x="1" y="1" width="52" height="38" fill="#ffffff"/><path d="M1 1l26 20L53 1" fill="none" stroke="#8a9099" stroke-width="2"/></svg>
  </div>
  <div class="abs band-text" style="left:384px;top:2090px">info@company.com</div>
  <div class="abs icon-box" style="left:700px;top:2060px">
    <svg width="50" height="50" viewBox="0 0 24 24"><path d="M6 3l3 0 2 5-2 2c1 2.5 3 4.5 5 5l2-2 5 2v3c0 1-1 2-2 2C10 20 4 14 4 5c0-1 1-2 2-2z" fill="#ffffff"/></svg>
  </div>
  <div class="abs band-text" style="left:830px;top:2090px">1234567890</div>
  <div class="abs footer-nav"><span class="active">Home</span><span>About Us</span><span>Services</span><span>Contact Us</span></div>

  <div class="abs bottombar">© 2015, All Rights Reserved</div>
  <div class="abs socials"><i></i><i></i><i></i><i></i><i></i></div>
</div>
</body>
</html>
```